Tall Fern Roofing Business Card

Need a business card with the logo that was designed here

Contact Information for Business Card

Name, Title, Phone, Email, Website, Company name

```html
<!DOCTYPE html>
<html lang="en">
<head>
<meta charset="utf-8">
<title>Tall Fern Roofing Business Card</title>
<link rel="stylesheet" href="https://fonts.googleapis.com/css2?family=Poppins:wght@400;600;700&display=swap">
<style>
  :root {
    --stage: #2a2a2b;
    --card-grey: #98999d;
    --card-black: #0c0c0d;
    --ink-white: #ffffff;
    --brand-blue: #2f7fcf;
    --divider: rgba(255,255,255,0.45);
  }
  * { margin: 0; padding: 0; box-sizing: border-box; }
  html, body {
    width: 1200px; height: 900px; overflow: hidden;
    background: var(--stage);
    font-family: "Poppins", sans-serif;
  }
  .stage { position: relative; width: 1200px; height: 900px; }
  .card {
    position: absolute;
    width: 560px; height: 320px;
    border-radius: 26px;
    overflow: hidden;
  }
  .card-front { left: 50px; top: 470px; background: var(--card-grey); }
  .card-back { left: 590px; top: 110px; background: var(--card-black); }

  .front-brand {
    position: absolute; left: 0; top: 0; width: 270px; height: 100%;
    display: flex; align-items: center; justify-content: center;
  }
  .brand-name {
    font-weight: 600; font-size: 26px; line-height: 1.15;
    color: var(--ink-white); text-align: center; letter-spacing: 0.5px;
  }
  .front-divider {
    position: absolute; left: 270px; top: 50px; width: 1px; height: 220px;
    background: var(--divider);
  }
  .front-details {
    position: absolute; left: 305px; top: 72px; color: var(--ink-white);
  }
  .person-name { font-weight: 700; font-size: 17px; letter-spacing: 0.5px; text-transform: uppercase; }
  .person-title { font-weight: 400; font-size: 13px; margin-bottom: 30px; }
  .contact-list { list-style: none; }
  .contact-item {
    display: flex; align-items: center; gap: 9px;
    font-size: 13px; line-height: 1.75;
  }
  .contact-item svg { width: 13px; height: 13px; flex: none; }

  .card-back .back-brand {
    position: absolute; inset: 0;
    display: flex; align-items: center; justify-content: center;
  }
  .card-back .brand-name { color: var(--brand-blue); font-size: 32px; }
</style>
</head>
<body>
<main class="stage">
  <section class="card card-front" aria-label="Business card front">
    <div class="front-brand"><p class="brand-name">Tall Fern<br>Roofing</p></div>
    <div class="front-divider"></div>
    <div class="front-details">
      <p class="person-name">Daniel Brooks</p>
      <p class="person-title">Managing Director</p>
      <ul class="contact-list">
        <li class="contact-item">
          <svg viewBox="0 0 16 16"><path fill="#fff" d="M3.5 1.5l2.5 0 1 3.5-1.8 1.2a8 8 0 0 0 4.6 4.6l1.2-1.8 3.5 1v2.5c0 .8-.7 1.5-1.5 1.5C7 14 2 9 2 3c0-.8.7-1.5 1.5-1.5z"/></svg>
          055-210 347 816
        </li>
        <li class="contact-item">
          <svg viewBox="0 0 16 16"><path fill="#fff" d="M1 3h14v10H1z"/><path fill="none" stroke="#98999d" stroke-width="1.3" d="M1.5 3.5L8 9l6.5-5.5"/></svg>
          hello@tallfern.com
        </li>
        <li class="contact-item">
          <svg viewBox="0 0 16 16"><circle cx="8" cy="8" r="6.5" fill="none" stroke="#fff" stroke-width="1.4"/><path fill="none" stroke="#fff" stroke-width="1.1" d="M1.5 8h13M8 1.5c-3 3.5-3 9.5 0 13M8 1.5c3 3.5 3 9.5 0 13"/></svg>
          www.tallfernroofing.com
        </li>
      </ul>
    </div>
  </section>

  <section class="card card-back" aria-label="Business card back">
    <div class="back-brand"><p class="brand-name">Tall Fern Roofing</p></div>
  </section>
</main>
</body>
</html>
```